Car transport business

We need a new business card design. Attached is our old card sample. I would just like to adjust the logo colors (blue and red) to be brighter. I changed my name to the brighter red and the word dispatcher to a brighter blue as an example. But you can adjust those colors further. And then perhaps you can use the same colors for the card design but use your imagination.

As a suggestion so the card stands out I would like to add a clip art of car carrier truck. Attached are examples of that as well

```html
<!DOCTYPE html>
<html lang="en">
<head>
<meta charset="utf-8">
<title>Northline Haul — Business Card</title>
<link href="https://fonts.googleapis.com/css2?family=Oswald:wght@500&family=Arimo:wght@400&display=swap" rel="stylesheet">
<style>
  :root {
    --backdrop: #101010;
    --card: #1b1b1c;
    --band-blue: #1e73c4;
    --brand-red: #e8202a;
    --brand-blue: #1e73c4;
    --text-light: #f2f2f2;
    --text-muted: #c9c9c9;
    --divider: #8a8a8a;
  }
  * { margin: 0; padding: 0; box-sizing: border-box; }
  html, body {
    width: 1200px; height: 900px; overflow: hidden;
    background: var(--backdrop);
  }
  .sheet {
    width: 1200px; height: 900px;
    display: flex; flex-direction: column; align-items: center; justify-content: center;
    gap: 40px;
  }
  .card {
    position: relative;
    width: 700px; height: 400px;
    background: var(--card);
    box-shadow: 0 10px 30px rgba(0,0,0,0.6);
    overflow: hidden;
  }
  .card__band {
    position: absolute; left: 0; right: 0; bottom: 0;
    height: 10px; background: var(--band-blue);
  }
  /* Front */
  .brand {
    position: absolute; inset: 0 0 10px 0;
    display: flex; align-items: center; justify-content: center; gap: 16px;
  }
  .brand__dot {
    width: 30px; height: 30px; border-radius: 50%;
    background: var(--brand-blue);
  }
  .brand__name {
    font-family: 'Oswald', sans-serif; font-weight: 500;
    font-size: 58px; letter-spacing: 3px; text-transform: uppercase;
    color: var(--brand-red); white-space: nowrap;
  }
  /* Back */
  .contact-side {
    position: absolute; inset: 0 0 10px 0;
    display: flex; align-items: center; justify-content: center;
    padding: 0 48px;
  }
  .person { text-align: right; flex: none; }
  .person__name {
    font-family: 'Oswald', sans-serif; font-weight: 500;
    font-size: 42px; line-height: 1.05; text-transform: uppercase;
    white-space: nowrap;
  }
  .person__first { color: var(--brand-blue); }
  .person__last { color: var(--brand-red); }
  .person__role {
    font-family: 'Arimo', sans-serif; font-size: 17px;
    color: var(--text-muted); margin-top: 2px;
  }
  .divider {
    width: 1px; height: 84px; background: var(--divider);
    margin: 0 24px; flex: none;
  }
  .contact-list { list-style: none; flex: none; }
  .contact-list li {
    display: flex; align-items: center; gap: 10px;
    font-family: 'Arimo', sans-serif; font-size: 17px;
    color: var(--text-light); line-height: 1.5; white-space: nowrap;
  }
  .contact-list svg { width: 17px; height: 17px; fill: var(--brand-blue); flex: none; }
</style>
</head>
<body>
<main class="sheet">
  <section class="card card--front">
    <div class="brand">
      <span class="brand__dot"></span>
      <span class="brand__name">Northline Haul</span>
    </div>
    <div class="card__band"></div>
  </section>

  <section class="card card--back">
    <div class="contact-side">
      <div class="person">
        <div class="person__name"><span class="person__first">Remy</span> <span class="person__last">Osterfeld</span></div>
        <div class="person__role">Dispatcher</div>
      </div>
      <div class="divider"></div>
      <ul class="contact-list">
        <li>
          <svg viewBox="0 0 24 24" aria-hidden="true"><path d="M6.6 10.8a15.1 15.1 0 0 0 6.6 6.6l2.2-2.2c.3-.3.7-.4 1-.2 1.1.4 2.3.6 3.6.6.6 0 1 .4 1 1V20c0 .6-.4 1-1 1A17 17 0 0 1 3 4c0-.6.4-1 1-1h3.5c.6 0 1 .4 1 1 0 1.3.2 2.5.6 3.6.1.3 0 .7-.2 1z"/></svg>
          555-014-2290
        </li>
        <li>
          <svg viewBox="0 0 24 24" aria-hidden="true"><path d="M7 3h10v4H7zM4 8h16a2 2 0 0 1 2 2v6h-4v4H6v-4H2v-6a2 2 0 0 1 2-2zm4 7v3h8v-3z"/></svg>
          555-014-7731
        </li>
        <li>
          <svg viewBox="0 0 24 24" aria-hidden="true"><path d="M2 5h20v14H2zm2 2v.5l8 5 8-5V7zm0 2.8V17h16V9.8l-8 5z"/></svg>
          northlinehaul@example.com
        </li>
      </ul>
    </div>
    <div class="card__band"></div>
  </section>
</main>
</body>
</html>
```